Counseling Practice Business Card

I need a professional looking business card incorporating my new logo that was just completed. Card needs to incorporate my name and title, description of my specialty, my address, my phone number, my fax number, my email and my website URL. I need to be able to choose design on/with different paper colors and textures.
I do not have a lot of business card ideas so I am open to anything but I want bold,sharp, clear card without additional designs other than my logo (see attached file info). I am open to different color backgrounds or paper colors including black. I do not like traditional brackets around area codes in phone number or dashes between numbers in phone number. Am open to other ways of presenting including periods between numbers as appropriate. I do not know enough to know what I like yet but I want card to coordinate and work together with my logo. My practice emphasizes natural mental health interventions so any use of color (with background paper color or the blue and green in my logo) that elicits nature is nice. In addition to black, any natural brown or wood looking background might be desirable also. Most of the offerings so far look very similar and boring.

Target Market(s)

Potential therapy clients and other professionals

Contact Information for Business Card

Card information:
Gerald M. Whitcombe, Ph.D.
Licensed Clinical Psychologist
Integrative Health Coach
4812 Marlowe Ridge Blvd SE
Suite 310
Fernhollow, GA 30718
(770) 415-2983 phone
(770) 581-4096 fax
drgeraldwhitcombe@quillmarsh.net
brightfernwellness.net

Font styles to use
Serif
Sans Serif
Other font styles liked:
• anything that you think looks crisp, clear and easily readable

Requirements
Must have
• Any color used should coordinate with my logo design (see attached files).
• Card should be printed horizontally so top and bottom are longest sides of rectangle.
• Background color or paper color should complement and highlight logo. Do not like a white background. black, grey, brown or any color my logo would blend well with.
Nice to have
• I would like designer to utilize color to highlight letters/name or phone-fax-web symbols.
• Bottom edge of card could be highlighted if appropriate to an idea.
Should not have
• I would NOT want the card to have a pure white background at all.
• No clear cards.
• Cards should be oriented with long sides on bottom and top, NOT sides. DO NOT LIKE THIS THIN TALL ORIENTATION.

```html
<!DOCTYPE html>
<html lang="en">
<head>
<meta charset="utf-8">
<title>Brightfern Wellness — Business Card</title>
<link rel="stylesheet" href="https://fonts.googleapis.com/css2?family=Libre+Baskerville:wght@400;700&family=Arimo:wght@400&display=swap">
<style>
  :root {
    --stage: #d9dadb;
    --blue: #2b7cc2;
    --blue-light: #4594d4;
    --green: #1d6b38;
    --paper: #f8f8f6;
    --ink: #555a5e;
    --rule: #a9abad;
    --white: #ffffff;
  }
  * { box-sizing: border-box; margin: 0; padding: 0; }
  html, body { width: 1200px; height: 960px; overflow: hidden; }
  body {
    background: var(--stage);
    font-family: "Arimo", Arial, sans-serif;
    position: relative;
  }
  .card {
    position: absolute;
    left: 250px;
    width: 700px;
    height: 400px;
    overflow: hidden;
    box-shadow: 0 6px 18px rgba(0,0,0,0.18);
  }
  /* Front */
  .card-front {
    top: 50px;
    background: linear-gradient(135deg, var(--blue) 0%, var(--blue-light) 100%);
  }
  .front-brand {
    position: absolute;
    left: 0; right: 0; top: 150px;
    display: flex; align-items: center; justify-content: center; gap: 16px;
  }
  .brand-dot {
    width: 22px; height: 22px; border-radius: 50%;
    background: var(--white);
  }
  .front-brand .brand-name {
    font-family: "Libre Baskerville", Georgia, serif;
    font-weight: 700;
    font-size: 44px;
    color: var(--white);
  }
  .front-url {
    position: absolute;
    right: 36px; bottom: 28px;
    font-size: 16px;
    color: var(--white);
  }
  /* Back */
  .card-back {
    top: 510px;
    background: var(--paper);
  }
  .back-brand {
    position: absolute;
    right: 50px; top: 40px;
    display: flex; align-items: center; gap: 10px;
  }
  .back-brand .brand-dot { width: 16px; height: 16px; background: var(--blue); }
  .back-brand .brand-name {
    font-family: "Libre Baskerville", Georgia, serif;
    font-weight: 700;
    font-size: 28px;
    color: var(--blue);
  }
  .person-name {
    position: absolute;
    left: 60px; top: 128px;
    font-family: "Libre Baskerville", Georgia, serif;
    font-weight: 700;
    font-size: 27px;
    color: var(--green);
  }
  .person-title {
    position: absolute;
    left: 60px; top: 170px;
    font-size: 17px;
    color: var(--ink);
  }
  .divider {
    position: absolute;
    left: 60px; right: 50px; top: 205px;
    height: 2px;
    background: var(--rule);
  }
  .contact-list {
    position: absolute;
    left: 60px; top: 224px;
    list-style: none;
    font-size: 17px;
    color: var(--ink);
  }
  .contact-list li {
    display: flex; align-items: center; gap: 10px;
    height: 27px;
  }
  .contact-list svg { width: 16px; height: 16px; fill: var(--green); flex: none; }
  .address {
    position: absolute;
    right: 50px; top: 232px;
    text-align: right;
    font-size: 18px;
    font-style: normal;
    line-height: 27px;
    color: var(--ink);
  }
  .edge {
    position: absolute; left: 0; bottom: 0;
    width: 700px; height: 400px;
  }
  .edge-blue { fill: var(--blue); }
  .edge-green { fill: var(--green); }
  .back-url {
    position: absolute;
    right: 40px; bottom: 16px;
    font-size: 19px;
    color: var(--white);
  }
</style>
</head>
<body>

<section class="card card-front">
  <div class="front-brand">
    <span class="brand-dot"></span>
    <span class="brand-name">Brightfern Wellness</span>
  </div>
  <p class="front-url">www.brightfernwellness.net</p>
</section>

<section class="card card-back">
  <svg class="edge" viewBox="0 0 700 400" aria-hidden="true">
    <path class="edge-green" d="M0 368 L440 368 L452 375 L0 375 Z"/>
    <path class="edge-blue" d="M0 384 L450 384 C470 384 475 346 505 346 L700 346 L700 400 L0 400 Z"/>
  </svg>

  <div class="back-brand">
    <span class="brand-dot"></span>
    <span class="brand-name">Brightfern Wellness</span>
  </div>

  <h1 class="person-name">Gerald M. Whitcombe, Ph.D.</h1>
  <p class="person-title">Licensed Clinical Psychologist/ Integrative Health Coach</p>
  <div class="divider"></div>

  <ul class="contact-list">
    <li>
      <svg viewBox="0 0 24 24" aria-label="Phone"><path d="M6.6 10.8a15.1 15.1 0 0 0 6.6 6.6l2.2-2.2c.3-.3.7-.4 1-.2 1.1.4 2.3.6 3.6.6.6 0 1 .4 1 1V20c0 .6-.4 1-1 1A17 17 0 0 1 3 4c0-.6.4-1 1-1h3.5c.6 0 1 .4 1 1 0 1.3.2 2.5.6 3.6.1.3 0 .7-.2 1z"/></svg>
      <span>770 415 2983</span>
    </li>
    <li>
      <svg viewBox="0 0 24 24" aria-label="Fax"><path d="M6 3h12v5H6zM4 9h16a2 2 0 0 1 2 2v6h-4v4H6v-4H2v-6a2 2 0 0 1 2-2zm4 7v3h8v-3z"/></svg>
      <span>770 581 4096</span>
    </li>
    <li>
      <svg viewBox="0 0 24 24" aria-label="Email"><path d="M2 5h20v14H2zm2 2v.5l8 5 8-5V7z"/></svg>
      <span>drgeraldwhitcombe@quillmarsh.net</span>
    </li>
  </ul>

  <address class="address">
    4812 Marlowe Ridge Blvd SE<br>
    Suite 310<br>
    Fernhollow, GA 30718
  </address>

  <p class="back-url">brightfernwellness.net</p>
</section>

</body>
</html>
```